Full book cover design for FEEDBACK book

The book title is: Feedback
Subtitle: Seek it, give it, connect with it.
Authors: Marcus Pellow & Corinne Abbot
We are looking for a complete book cover design using a combination of my brand colours and that of my co-author (Marcus). The colours we use include:

Corinne: Blue #1E84AB & Marcus: Blue #01275B and white.

An idea on the wording for the back cover is here (open to tweak/shorten it if better that way):

The most dynamic leaders today are focused on increasing effectiveness and improving team cohesion. This book demonstrates how creating a culture of feedback enables both of these things.

Feedback allows for the strengthening of communication and allows individuals to continually learn and grow, with the support of their colleagues.

Corinne and Marcus have created a unique approach to change the often-negative perception associated with feedback. They created it for you…to unlock the opportunity, freedom and success you can achieve when feedback is implemented and used regularly.

If you are a leader looking for ways to build skills in your people, contribute to their growth and development, and maintain a strong, supportive culture, all while delivering business outcomes, then this is the book for you.

“If you are keen to transform feedback from average to awesome and from being a chore to an art, this book is a must read.”
Victor Lanstrom, Bramwell Axleworks

“In today’s hybrid work environment, greater transparency and empowerment, through developing a feedback culture, is essential.”
Tamsin Lowry, Velnor

We will also need to allow space for a barcode and the publishers logo (just above it) on the back bottom right hand side.

Target Market(s)

Business leaders

Industry/Entity Type

Business

Font styles to use
Serif
Other font styles liked:
• Open to any other fonts that will suit the design

Colors
0054AA
0677BA
7BADD7
CADEEF
E8F1F8

Requirements
Must have
• Colours: Blue #1E84AB & Blue #01275B and white.
Nice to have
• Something creative and smart but not too busy.

```html
<!DOCTYPE html>
<html lang="en">
<head>
<meta charset="utf-8">
<title>Feedback — Full Book Cover</title>
<link rel="stylesheet" href="https://fonts.googleapis.com/css2?family=Noto+Serif:wght@400;500&display=swap">
<style>
  :root {
    --blue: #1E84AB;
    --navy: #01275B;
    --title-blue: #16628F;
    --white: #FFFFFF;
  }
  html, body {
    margin: 0;
    padding: 0;
    width: 1200px;
    height: 874px;
    overflow: hidden;
    background: var(--white);
  }
  .cover {
    position: relative;
    width: 1200px;
    height: 874px;
    font-family: "Noto Serif", Georgia, serif;
    overflow: hidden;
  }

  /* Back cover + spine */
  .back {
    position: absolute;
    left: 0; top: 0;
    width: 620px; height: 874px;
    background: var(--blue);
  }
  .back-bubble {
    position: absolute;
    left: 225px; top: 40px;
    width: 128px; height: 112px;
  }
  .back-title {
    position: absolute;
    left: 0; width: 577px;
    top: 142px;
    margin: 0;
    text-align: center;
    font-weight: 400;
    font-size: 38px;
    color: var(--navy);
  }
  .blurb {
    position: absolute;
    left: 37px; top: 240px;
    width: 500px;
    color: var(--white);
    font-size: 14px;
    letter-spacing: -0.35px;
    line-height: 14.5px;
  }
  .blurb p {
    margin: 0 0 14.5px;
    text-align: justify;
    text-align-last: center;
  }
  .blurb .attribution {
    display: block;
    text-align: center;
    text-transform: uppercase;
  }
  .barcode-space {
    position: absolute;
    left: 367px; top: 721px;
    width: 187px; height: 111px;
    background: var(--white);
  }
  .spine-title,
  .spine-authors {
    position: absolute;
    margin: 0;
    color: var(--white);
    font-weight: 400;
    writing-mode: vertical-rl;
    white-space: nowrap;
  }
  .spine-title {
    left: 580px; top: 58px;
    font-size: 39px;
    line-height: 40px;
  }
  .spine-authors {
    left: 589px; top: 546px;
    font-size: 18px;
    line-height: 20px;
  }

  /* Front cover */
  .front {
    position: absolute;
    left: 620px; top: 0;
    width: 580px; height: 874px;
    background: var(--white);
  }
  .front-bubble {
    position: absolute;
    left: 142px; top: 166px;
    width: 305px; height: 277px;
  }
  .front-title {
    position: absolute;
    left: 100px; width: 394px;
    top: 440px;
    margin: 0;
    text-align: center;
    font-weight: 500;
    font-size: 88px;
    line-height: 1;
    color: var(--title-blue);
    white-space: nowrap;
  }
  .paper-strip {
    position: absolute;
    left: 0; top: 598px;
    width: 525px; height: 108px;
  }
  .subtitle {
    position: absolute;
    left: 100px; top: 636px;
    width: 372px;
    margin: 0;
    text-align: center;
    font-size: 19px;
    font-weight: 400;
    color: var(--navy);
    white-space: nowrap;
  }
  .author-band {
    position: absolute;
    left: 0; top: 775px;
    width: 580px; height: 60px;
    background: var(--blue);
    display: flex;
    align-items: center;
    justify-content: center;
  }
  .author-band p {
    margin: 0;
    color: var(--white);
    font-size: 23px;
    padding-left: 30px;
  }
</style>
</head>
<body>
<div class="cover">

  <section class="back">
    <svg class="back-bubble" viewBox="0 0 128 112" role="img" aria-label="Speech bubble made of many small chat icons">
      <path d="M6 4 H118 Q122 4 122 10 V82 L124 110 L104 84 H8 Q4 84 4 78 V10 Q4 4 10 4 Z" fill="#143F74"/>
    </svg>
    <h2 class="back-title">Feedback</h2>

    <div class="blurb">
      <p>The most dynamic leaders today are focused on increasing effectiveness and improving team cohesion. This book demonstrates how creating a culture of feedback enables both of these things.</p>
      <p>Feedback allows for the strengthening of communication and allows individuals to continually learn and grow, with the support of their colleagues.</p>
      <p>Corinne and Marcus have created a unique approach to change the often-negative perception associated with feedback. They created it for you…to unlock the opportunity, freedom and success you can achieve when feedback is implemented and used regularly.</p>
      <p>If you are a leader looking for ways to build skills in your people, contribute to their growth and development, and maintain a strong, supportive culture, all while delivering business outcomes, then this is the book for you.</p>
      <p class="quote">“If you are keen to transform feedback from average to awesome and from being a chore to an art, this book is a must read.”
        <span class="attribution">Victor Lanstrom, Bramwell Axleworks</span></p>
      <p class="quote">“In today’s hybrid work environment, greater transparency and empowerment, through developing a feedback culture, is essential.”
        <span class="attribution">Tamsin Lowry, Velnor</span></p>
    </div>

    <div class="barcode-space"></div>

    <h2 class="spine-title">Feedback</h2>
    <p class="spine-authors">Marcus Pellow &amp; Corinne Abbot</p>
  </section>

  <section class="front">
    <svg class="front-bubble" viewBox="0 0 305 277" role="img" aria-label="Large speech bubble made of many small chat and profile icons in navy and teal">
      <defs>
        <linearGradient id="bubbleTone" x1="0" y1="0" x2="1" y2="1">
          <stop offset="0" stop-color="#1B4C82"/>
          <stop offset="1" stop-color="#2A8FB0"/>
        </linearGradient>
      </defs>
      <path d="M14 4 H282 Q292 4 292 14 V204 L304 276 L268 214 H14 Q4 214 4 204 V14 Q4 4 14 4 Z" fill="url(#bubbleTone)"/>
    </svg>

    <h1 class="front-title">Feedback</h1>

    <svg class="paper-strip" viewBox="0 0 525 108" aria-hidden="true">
      <defs>
        <filter id="stripShadow" x="-5%" y="-30%" width="110%" height="160%">
          <feDropShadow dx="0" dy="4" stdDeviation="6" flood-color="#000" flood-opacity="0.18"/>
        </filter>
      </defs>
      <rect x="0" y="8" width="525" height="92" fill="#F3F3F3" filter="url(#stripShadow)"/>
      <path d="M108 14 L410 12 L410 92 L108 94 Z" fill="#FFFFFF"/>
      <rect x="96" y="10" width="16" height="92" rx="6" fill="#E6E6E6"/>
      <rect x="408" y="8" width="16" height="92" rx="6" fill="#E6E6E6"/>
    </svg>
    <p class="subtitle">SEEK IT, GIVE IT, CONNECT WITH IT</p>

    <div class="author-band">
      <p>Marcus Pellow &amp; Corinne Abbot</p>
    </div>
  </section>

</div>
</body>
</html>
```